Business Card Design

Company is a Commercial Building Company specialising in New Construction and existing refurbishments

Industry/Entity Type

Business

Contact Information for Business Card

Liam Porter
Construction Manager
E Liam@marshbuilding.com.au
M 0400 213 594
Mail 14 Tarrant Rise Brindle Bay WA 6219

```html
<!DOCTYPE html>
<html lang="en">
<head>
<meta charset="utf-8">
<title>Marsh Building &amp; Construction – Business Cards</title>
<link href="https://fonts.googleapis.com/css2?family=Exo+2:wght@300;400;600;700&display=swap" rel="stylesheet">
<style>
  :root {
    --teal: #18b8cc;
    --teal-light: #7fe0ec;
    --teal-deep: #10a6ba;
    --gold: #e9a825;
    --navy: #2d3548;
    --grey: #4a4f5a;
    --paper: #ffffff;
    --paper-shade: #eeeeee;
    --backdrop: #e4e1dc;
  }
  * { margin: 0; padding: 0; box-sizing: border-box; }
  html, body { width: 1200px; height: 858px; overflow: hidden; }
  body {
    background: var(--backdrop);
    font-family: "Exo 2", "Helvetica Neue", Arial, sans-serif;
    position: relative;
  }
  .card {
    position: absolute;
    border-radius: 4px;
    box-shadow: 0 14px 30px rgba(0,0,0,0.22);
    overflow: hidden;
  }

  /* Front */
  .card-front {
    left: 70px; top: 264px;
    width: 540px; height: 330px;
    background: radial-gradient(ellipse at 48% 55%, var(--teal-light) 0%, var(--teal) 55%, var(--teal-deep) 100%);
    display: flex; flex-direction: column; justify-content: center;
    padding-left: 52px;
  }
  .front-wordmark {
    color: var(--paper);
    text-transform: uppercase;
    line-height: 1.05;
    font-weight: 400;
  }
  .front-wordmark .line-main { display: block; font-size: 52px; font-weight: 700; letter-spacing: 0.5px; }
  .front-wordmark .line-sub { display: block; font-size: 46px; font-weight: 300; letter-spacing: 0.5px; margin-left: 30px; }

  /* Back */
  .card-back {
    left: 730px; top: 159px;
    width: 330px; height: 540px;
    background: linear-gradient(160deg, var(--paper) 0%, var(--paper-shade) 100%);
    padding: 74px 30px 0 40px;
  }
  .brand {
    display: flex; align-items: center; gap: 12px;
    margin-bottom: 58px;
  }
  .brand-mark { width: 22px; height: 22px; background: var(--gold); flex: none; }
  .brand-name {
    color: var(--navy);
    font-weight: 700;
    font-size: 22px;
    line-height: 1.05;
    text-transform: uppercase;
  }
  .details { padding-left: 54px; }
  .person-name {
    color: var(--gold);
    font-weight: 700;
    font-size: 24px;
    text-transform: uppercase;
    letter-spacing: 0.5px;
    line-height: 1.1;
  }
  .person-role { color: var(--grey); font-size: 14px; margin-top: 2px; }
  .contact { margin-top: 60px; color: var(--grey); font-size: 15px; line-height: 1.45; }
  .address { margin-top: 34px; color: var(--grey); font-size: 17px; line-height: 1.3; }
  .base-rule {
    position: absolute; left: 0; right: 0; bottom: 46px;
    height: 2px; background: var(--gold);
  }
  .base-band {
    position: absolute; left: 0; right: 0; bottom: 0;
    height: 40px; background: var(--teal);
  }
</style>
</head>
<body>
  <section class="card card-front" aria-label="Card front">
    <h1 class="front-wordmark">
      <span class="line-main">Marsh Building</span>
      <span class="line-sub">&amp; Construction</span>
    </h1>
  </section>

  <section class="card card-back" aria-label="Card back">
    <div class="brand">
      <span class="brand-mark" aria-hidden="true"></span>
      <span class="brand-name">Marsh Building<br>&amp; Construction</span>
    </div>
    <div class="details">
      <p class="person-name">Liam Porter</p>
      <p class="person-role">Construction Manager</p>
      <p class="contact">0400 213 594<br>Liam@marshbuilding.com.au</p>
      <p class="address">14 Tarrant Rise<br>Brindle Bay WA 6219</p>
    </div>
    <div class="base-rule"></div>
    <div class="base-band"></div>
  </section>
</body>
</html>
```